Accounting firm needing business card / letterhead designed
Marcus L. Trenholm, CPA
marcus@veltrowledger.com
www.veltrowledger.com
842 E Alder Ave Halvern, OR 43827
419-562-0974

```html
<!DOCTYPE html>
<html lang="en">
<head>
<meta charset="utf-8">
<title>Veltrow Ledger – Business Card</title>
<link href="https://fonts.googleapis.com/css2?family=Open+Sans:wght@400;600&display=swap" rel="stylesheet">
<style>
  :root {
    --page-bg: #3b3532;
    --card-black: #0d0d0d;
    --accent-green: #8cc63f;
    --brand-indigo: #3b3a8f;
    --text-white: #f2f2f2;
    --silver: #c9c9c9;
  }
  * { margin: 0; padding: 0; box-sizing: border-box; }
  html, body {
    width: 1200px; height: 900px; overflow: hidden;
    background: var(--page-bg);
    font-family: "Open Sans", Arial, sans-serif;
  }
  .sheet {
    width: 1200px; height: 900px;
    display: flex; align-items: center; justify-content: center; gap: 60px;
  }
  .card {
    width: 520px; height: 297px;
    background: var(--card-black);
    position: relative;
    box-shadow: 0 10px 30px rgba(0,0,0,.45);
  }
  .card-front { display: flex; align-items: center; }
  .brand-block {
    width: 250px; height: 100%;
    display: flex; align-items: center; justify-content: center;
  }
  .brand-name {
    color: var(--brand-indigo);
    font-weight: 600; font-size: 27px; letter-spacing: 1px;
    text-transform: uppercase; line-height: 1.05; text-align: left;
  }
  .divider {
    width: 1px; height: 170px;
    background: linear-gradient(to bottom, transparent, var(--accent-green) 20%, var(--accent-green) 80%, transparent);
  }
  .contact-block { padding-left: 26px; padding-right: 12px; color: var(--text-white); }
  .person-name {
    color: var(--accent-green);
    font-weight: 600; font-size: 17px; text-transform: uppercase;
    margin-bottom: 6px; white-space: nowrap;
  }
  .contact-list { list-style: none; font-size: 12.5px; line-height: 1.55; }
  .contact-list li { display: flex; align-items: center; gap: 6px; white-space: nowrap; }
  .contact-list svg { width: 11px; height: 11px; flex: none; }
  .address { font-size: 12.5px; line-height: 1.55; margin-top: 14px; }
  .card-back { display: flex; align-items: center; justify-content: center; }
  .back-brand {
    color: var(--silver);
    font-weight: 600; font-size: 40px; letter-spacing: 2px;
    text-transform: uppercase; white-space: nowrap;
  }
</style>
</head>
<body>
<main class="sheet">
  <section class="card card-front" aria-label="Business card front">
    <div class="brand-block">
      <p class="brand-name">Veltrow<br>Ledger</p>
    </div>
    <div class="divider"></div>
    <div class="contact-block">
      <h1 class="person-name">Marcus L. Trenholm, CPA</h1>
      <ul class="contact-list">
        <li>
          <svg viewBox="0 0 12 12" aria-hidden="true"><path fill="#8cc63f" d="M2.5 1l2 2-1 1.3c.6 1.4 1.8 2.6 3.2 3.2L8 6.5l2 2-1 2C5 10 2 7 1.5 3z"/></svg>
          555-562-0974
        </li>
        <li>
          <svg viewBox="0 0 12 12" aria-hidden="true"><rect x="1" y="2.5" width="10" height="7" fill="#8cc63f"/><path d="M1 2.5l5 4 5-4" stroke="#0d0d0d" stroke-width="1" fill="none"/></svg>
          marcus@veltrowledger.com
        </li>
        <li>
          <svg viewBox="0 0 12 12" aria-hidden="true"><circle cx="6" cy="6" r="5" fill="#8cc63f"/><path d="M1 6h10M6 1c-2 2.5-2 7.5 0 10M6 1c2 2.5 2 7.5 0 10" stroke="#0d0d0d" stroke-width=".8" fill="none"/></svg>
          www.veltrowledger.com
        </li>
      </ul>
      <p class="address">842 E Alder Ave Halvern,<br>OR 43827</p>
    </div>
  </section>

  <section class="card card-back" aria-label="Business card back">
    <p class="back-brand">Veltrow Ledger</p>
  </section>
</main>
</body>
</html>
```